Design a compelling Tarnwove Business Card that will drive people to my site

I want a business card that I can give to people—less to tell them who I am and more to direct them to my website. My website is a portal for Pelmor Aquatics Officials and a place for people who want to become Pelmor Aquatics Officials.
I am uploading my official company logo as well as a business card mockup that I did on my own. Please feel free to completely stray from this design.
I've included a screen recording of the homepage of my website as well.
Target Market(s)
Pelmor Aquatics Officials and people who desire to become one
Contact Information for Business Card
website url
Look and feel
Each slider illustrates characteristics of the customer's brand and the style your logo design should communicate.

```html
<!DOCTYPE html>
<html lang="en">
<head>
<meta charset="UTF-8">
<title>Tarnwove Business Card</title>
<link rel="stylesheet" href="https://fonts.googleapis.com/css2?family=Montserrat:wght@400;500;600;700&display=swap">
<style>
  :root {
    --backdrop: #1d1e21;
    --brand-blue: #7587ad;
    --paper-grey: #d3d3d5;
    --ink-navy: #2b3a88;
    --ink-soft: #7d8ab6;
    --on-blue: #dddfe6;
    --card-radius: 22px;
  }
  * { margin: 0; padding: 0; box-sizing: border-box; }
  html, body {
    width: 1200px;
    height: 800px;
    overflow: hidden;
    background: var(--backdrop);
    font-family: "Montserrat", sans-serif;
  }
  .card-set {
    width: 1200px;
    height: 800px;
    display: flex;
    align-items: center;
    justify-content: center;
    gap: 48px;
  }
  .card {
    position: relative;
    width: 520px;
    height: 298px;
    border-radius: var(--card-radius);
    overflow: hidden;
    box-shadow: 0 14px 30px rgba(0,0,0,0.45);
  }
  /* Front: contact side */
  .card--front { background: var(--paper-grey); }
  .card--front .wave {
    position: absolute;
    inset: 0;
    width: 100%;
    height: 100%;
  }
  .card--front .wave path { fill: var(--brand-blue); }
  .front-wordmark {
    position: absolute;
    left: 44px;
    top: 58px;
    font-size: 34px;
    font-weight: 600;
    letter-spacing: -0.5px;
    color: var(--on-blue);
  }
  .contact {
    position: absolute;
    left: 268px;
    top: 118px;
  }
  .contact__name {
    font-size: 24px;
    font-weight: 700;
    color: var(--ink-navy);
    line-height: 1.1;
  }
  .contact__role {
    margin-top: 4px;
    font-size: 15px;
    font-weight: 500;
    color: var(--ink-soft);
  }
  .contact__rule {
    width: 22px;
    height: 3px;
    background: var(--ink-navy);
    margin: 12px 0 12px;
  }
  .contact__line {
    font-size: 14px;
    font-weight: 500;
    color: var(--ink-soft);
    line-height: 1.45;
  }
  /* Back: website side */
  .card--back {
    background: var(--brand-blue);
    display: flex;
    flex-direction: column;
    justify-content: center;
    padding-left: 58px;
  }
  .site-url {
    font-size: 58px;
    font-weight: 600;
    letter-spacing: -1px;
    color: var(--on-blue);
    line-height: 1;
  }
  .site-rule {
    width: 150px;
    height: 2px;
    background: var(--on-blue);
    margin: 18px 0 0 140px;
  }
  .tagline {
    margin-top: 12px;
    font-size: 17px;
    font-weight: 500;
    color: var(--on-blue);
  }
</style>
</head>
<body>
  <main class="card-set">
    <section class="card card--front" aria-label="Contact side">
      <svg class="wave" viewBox="0 0 520 298" preserveAspectRatio="none" aria-hidden="true">
        <path d="M0 0 H330 C300 90 250 120 210 150 C170 180 140 210 110 298 H0 Z"/>
      </svg>
      <div class="front-wordmark">tarnwove</div>
      <div class="contact">
        <p class="contact__name">Marcus Fenwold</p>
        <p class="contact__role">CEO &amp; Founder</p>
        <div class="contact__rule"></div>
        <p class="contact__line">marcus@tarnwove.com</p>
        <p class="contact__line">(555) 201 - 4473</p>
      </div>
    </section>

    <section class="card card--back" aria-label="Website side">
      <p class="site-url">tarnwove.com</p>
      <div class="site-rule"></div>
      <p class="tagline">Your Poolside Referee's Gateway</p>
    </section>
  </main>
</body>
</html>
```